Exclusive beauty salon needs a price list or services booklet

I need a new very attractive flyer for my beauty salon, containing information on the different services and their prices.
In attachment you can find a pdf of the "old" one, but I'd love to have a beautifully designed new one!
I'd love to have a booklet in format 148 x 148 mm, or in US format, containing 12 or 16 pages, but if you can offer other nice looking designs they are welcome!
The services that need to come in the booklet with their prices can all be found on my website: www.atelierverano.be, starting with
Gelaatsverzorging
Wimperverlenging
Suikerontharing
Wimperlifting
Permanente Make Up
Airbrush Tanning

Target Market(s)

woman from 20 to 89 years old

Industry/Entity Type

Beauty Salon

Font styles to use
Sans Serif

Colors

Designer to choose colors to be used in the design.

Requirements
Must have
• a classy nice look, it must contain details about the services from my beauty salon and their prices, and nice pictures.
• The Names, prices and explanations of the services can easily be found on my website: www.atelierverano.be
Nice to have
• In attachment you can find the "old" price list in pdf, what I need now is a "new booklet" with the new logo and updated services price list.
• I need a very nice and attractive looking booklet, classy chique, Paris chique, looking very expensive.
Should not have
• Not too much colors, not too curly, but still feminine

```html
<!DOCTYPE html>
<html lang="nl">
<head>
<meta charset="utf-8">
<title>Airbrush Tanning – Prijsboekje</title>
<link href="https://fonts.googleapis.com/css2?family=Questrial&display=swap" rel="stylesheet">
<style>
  :root{
    --backdrop:#a4a4a4;
    --paper:#ffffff;
    --paper-shade:#eeeeee;
    --teal:#5fbab6;
    --teal-band:#7cc8c4;
    --ink:#6b6b6b;
    --ink-dark:#4a4a4a;
  }
  *{margin:0;padding:0;box-sizing:border-box}
  html,body{width:1200px;height:523px;overflow:hidden;background:var(--backdrop)}
  body{font-family:"Questrial",sans-serif;color:var(--ink);position:relative}

  .spread{position:absolute;left:259px;top:88px;width:682px;height:343px;display:flex}
  .page{position:relative;width:341px;height:343px;background:var(--paper);overflow:hidden}
  .page--left{background:linear-gradient(90deg,#f7f7f7 0%,var(--paper) 30%,var(--paper) 85%,var(--paper-shade) 100%)}
  .page--right{background:linear-gradient(90deg,#e2e2e2 0%,var(--paper) 10%,#f9f9f9 100%)}

  .section-title{position:absolute;left:42px;top:15px;font-size:12.5px;letter-spacing:.2px;color:var(--teal);font-weight:400}
  .body-copy{font-size:5.6px;line-height:7.2px;color:var(--ink)}
  .body-copy h3{font-size:5.6px;font-weight:400;color:var(--ink-dark);letter-spacing:.2px}
  .body-copy p{margin-bottom:7px}

  .prep{position:absolute;left:42px;top:32px;width:138px}

  .portrait{position:absolute;left:186px;top:112px;width:190px;height:231px;z-index:2;
    background:radial-gradient(ellipse 34% 40% at 50% 42%,#e9c2a8 0%,#dcae8c 55%,rgba(220,174,140,0) 100%),
      linear-gradient(90deg,rgba(255,255,255,0) 0%,#d8b27a 20%,#caa066 50%,#d8b27a 80%,rgba(255,255,255,0) 100%);}

  .price-band{position:absolute;left:33px;top:16px;right:0;height:14px;background:var(--teal-band);color:#fff;
    font-size:9.5px;line-height:14px;padding-left:21px}
  .price-band .price{position:absolute;left:248px;top:0;font-size:8px}

  .treatment{position:absolute;left:41px;top:42px;width:277px}
  .treatment h3{margin-top:0}
  .treatment .aftercare{margin-top:4px}

  .spray-photo{position:absolute;left:44px;top:196px;width:92px;height:92px;border-radius:50%;
    background:radial-gradient(circle at 35% 55%,#d9925c 0%,#e7b48a 40%,#f2f2f2 75%)}

  .brand{position:absolute;left:292px;top:306px;font-size:6px;letter-spacing:.8px;color:var(--ink-dark);display:flex;align-items:center;gap:4px}
  .brand .mark{width:5px;height:5px;border-radius:50%;background:var(--ink-dark)}
</style>
</head>
<body>
<main class="spread">
  <section class="page page--left">
    <h1 class="section-title">AIRBRUSH TANNING</h1>
    <div class="prep body-copy">
      <h3>DE VOORBEREIDING</h3>
      <p>De dag van de afspraak kan je beter geen vette of oliehoudende producten op het lichaam aanbrengen. Een goede scrubbeurt (op waterbasis, zonder olie !) zal ervoor zorgen dat de kleur mooi egaal en gelijkmatig verdeeld wordt en belangrijker nog, dat je huid veel langer bruin zal blijven. De loszittende dode huidcellen worden verwijderd bij het scrubben. Degene die nog vast zitten zullen nog veel langer op hun plaats blijven. Opgelet : indien je zelf de scrub uitvoert, zorg ervoor dat je geen stukjes vergeet !</p>
      <p>Trek donkere loszittende kledij aan. Op lichte kledij kan de gekleurde component licht kleur afgeven. Dit laat zich volledig verwijderen in de was. De kledij mag niet spannen en vooral geen wrijving op de huid geven. De component die de uiteindelijke kleur moet geven werkt gedurende ongeveer 12 uur verder. Op plaatsen waar de kledij op de huid schuurt kan het product vroegtijdig weggewreven worden en dus lichtere strepen geven.</p>
      <p>Het product laat geen vlekken na op de kledij. Alleen op de materialen van zeer fijne lingerie kan het het eventueel inwerken.</p>
      <p>Het product werkt heel goed in op nagels (is een verhoorning van de huid en bestaat dus ook uit dode keratine huidcellen) ! Wij proberen deze zo veel mogelijk te sparen bij het spuiten. Om helemaal zeker te zijn, vooral bij veelvuldige herhalingen, kan je beter je nagels lakken, eventueel met een kleurloze nagellak. Let wel op dat je geen huid bedekt met de lak.</p>
    </div>
  </section>

  <section class="page page--right">
    <h2 class="price-band">Airbrush tanning van het volledige lichaam <span class="price">€29</span></h2>
    <div class="treatment body-copy">
      <h3>DE AIRBRUSH TANNING ZELF</h3>
      <p>Je huid wordt ingespoten met het product. Je ziet onmiddellijk het resultaat. Eventueel wordt in verschillende lagen gespoten zodat je zeker niet te bruin kan worden. Het inspuiten van het volledig lichaam duurt ongeveer 10 minuten. Daarna moet je alvorens de kleren aan te trekken nog een kwartiertje het product laten indrogen. Je verlaat het instituut met een mooie, gezonde bruine kleur.</p>
      <h3 class="aftercare">DE NAZORG</h3>
      <p>Gedurende de eerste 8 uren na de airbrush tanning kan je best voorkomen om hevig te zweten. Dus best geen sport of andere zware inspanningen. Je mag niet douchen ! Tijdens deze eerste 8 uren kan het product een lichte kleur afgeven op kledij of lakens. Deze verdwijnt zonder problemen in de was. Na 8 uur mag je douchen. De tijdelijke kleurcomponent spoelt volledig weg. Ondertussen heeft je huid een mooie bruine kleur gekregen. Hoe beter je je huid hydrateert hoe langer je de kleur kan behouden. De kleur blijft gemiddeld tussen de 7 dagen en 10 dagen naargelang je huidtype. Daarna begint de kleur te vervagen.</p>
    </div>
    <div class="spray-photo" role="img" aria-label="Foto van een buik die met een airbrush-pistool gebruind wordt"></div>
    <div class="brand"><span class="mark"></span>ATELIER VERANO</div>
  </section>

  <div class="portrait" role="img" aria-label="Portretfoto van een blonde vrouw, half gebruind en half naturel"></div>
</main>
</body>
</html>
```